Intelligent design image for our website

I would like an awesome image for our website that showcases the intelligent design of our app. We currently have a test web site here.
https://www.corvinta.com.au/test-ewd/
I really do not like the graphic next to the "Intelligent design" and i want something much better than this.
Our app is used by Australian Truck Drivers. It would be nice to have a little bit of an Australian feel, but most importantly is should clearly showcase our app look a feel and the screens should be as legible (readable) as possible. These examples could be used for inspiration.
https://pixelmarrow.net/products/free-app-showcase-mockup-psd-5170284
https://www.plonkit.com/community/file/2640519873320957716/PhoneSuite-Landing-Page-Template-for-Mobile-Apps-Showcase

```html
<!DOCTYPE html>
<html lang="en">
<head>
<meta charset="utf-8">
<title>Driver Compliance App Screens</title>
<link href="https://fonts.googleapis.com/css2?family=PT+Sans:wght@400;700&display=swap" rel="stylesheet">
<style>
:root{
  --bg:#ffffff;
  --ring:#eef1f8;
  --ring-edge:#dfe5f1;
  --green:#12a81c;
  --green-soft:#1fd98a;
  --blue:#2b96e0;
  --blue-light:#9cc0f5;
  --blue-dark:#1f66e0;
  --red:#e2312f;
  --ink:#1d1f24;
  --muted:#5b6070;
  --line:#e3e6ec;
  --card:#ffffff;
  --screen:#f4f5f8;
}
*{box-sizing:border-box;margin:0;padding:0}
html,body{width:1200px;height:909px;overflow:hidden;background:var(--bg);font-family:"PT Sans",sans-serif;color:var(--ink)}
.canvas{position:relative;width:1200px;height:909px;overflow:hidden}
.rings{position:absolute;left:0;top:0}
.backdrop{position:absolute;left:146px;top:108px;width:676px;height:676px;border-radius:50%;
  background:radial-gradient(circle at 25% 85%,var(--green-soft) 0%,var(--green) 45%,#0aa21a 100%)}
.screen{position:absolute;top:92px;width:300px;height:726px;background:var(--screen);border-radius:28px;overflow:hidden;
  box-shadow:0 18px 40px rgba(20,40,80,.18)}
.screen.left{left:170px}
.screen.right{left:500px}
.status{display:flex;justify-content:space-between;align-items:center;padding:12px 20px 4px;font-weight:700;font-size:13px;background:#fff}
.status .icons{display:flex;gap:4px;align-items:center}
.header{display:flex;align-items:flex-start;gap:10px;padding:6px 14px 10px;background:#fff;border-bottom:1px solid var(--line)}
.header .menu{width:14px;margin-top:14px}
.header .menu i{display:block;height:2px;background:var(--ink);margin:3px 0}
.header .menu i:last-child{width:9px}
.driver{flex:1;min-width:0}
.driver .name{font-size:15px;font-weight:700;white-space:nowrap}
.driver .licence{font-size:12px;color:var(--muted);white-space:nowrap}
.sync{display:flex;flex-direction:column;align-items:center;gap:3px}
.sync-btn{background:var(--blue);color:#fff;font-size:11px;padding:3px 8px;border-radius:4px;white-space:nowrap}
.body{padding:6px 8px}
.card{background:var(--card);border-radius:6px;box-shadow:0 1px 4px rgba(0,0,0,.08);margin-bottom:8px;padding:6px 8px 8px}
.titled{margin-top:18px;border-top:3px solid var(--blue);position:relative;padding-top:18px}
.tab{position:absolute;top:-14px;left:50%;transform:translateX(-50%);background:var(--blue);color:#fff;font-size:12px;
  padding:4px 16px;border-radius:0 0 10px 10px;white-space:nowrap;display:flex;gap:5px;align-items:center}
.info{position:absolute;right:6px;top:4px;width:14px;height:14px;border:1.5px solid var(--blue);border-radius:50%;color:var(--blue);
  font-size:9px;font-weight:700;text-align:center;line-height:11px}
.grid{display:grid;grid-template-columns:1fr 1fr}
.cell{text-align:center;padding:5px 2px;border-bottom:1px solid var(--line)}
.cell:nth-child(odd){border-right:1px solid var(--line)}
.value{font-size:13px;font-weight:700}
.label{font-size:9px;color:var(--muted);line-height:1.15}
.pager{display:flex;justify-content:space-between;align-items:center;padding-top:6px}
.btn{border:1px solid var(--blue);color:var(--blue);font-size:9px;padding:2px 10px;border-radius:3px;white-space:nowrap}
.pager .mid{text-align:center}
.range{display:flex;justify-content:space-between;padding:0 4px 6px;border-bottom:2px solid var(--blue)}
.range .end{text-align:right}
.bar{margin:10px 0 2px;height:8px;border-radius:4px;background:var(--blue-light);position:relative}
.bar span{position:absolute;left:0;top:0;bottom:0;border-radius:4px;background:var(--blue-dark)}
.bar-labels{display:flex;justify-content:space-between;font-size:8px;color:var(--muted)}
.bar-title{font-size:9px;color:var(--muted);margin-top:6px}
.calendar{display:grid;grid-template-columns:repeat(7,1fr);gap:5px 0;justify-items:center;padding:8px 0 4px}
.day{width:22px;height:22px;border-radius:50%;border:1.5px solid var(--blue);color:var(--blue);font-size:9px;
  display:flex;align-items:center;justify-content:center;position:relative}
.day.miss{border-color:var(--red);color:var(--red)}
.day.miss::after{content:"";position:absolute;width:26px;height:1.5px;background:var(--red);transform:rotate(45deg)}
.day.now{background:var(--blue);color:#fff}
.day.ok::after{content:"";position:absolute;right:-3px;top:-3px;width:8px;height:8px;border-radius:50%;background:var(--green)}
.note{font-size:9px;color:var(--ink);line-height:1.25}
.foot{font-size:8px;color:var(--muted);line-height:1.2;padding-top:4px}
.tabbar{position:absolute;left:0;right:0;bottom:0;height:50px;background:#fff;border-top:1px solid var(--line);display:flex;justify-content:space-around;align-items:center}
.tabitem{display:flex;flex-direction:column;align-items:center;font-size:10px;font-weight:700;gap:2px}
.home-bar{position:absolute;bottom:5px;left:50%;transform:translateX(-50%);width:100px;height:4px;border-radius:2px;background:var(--ink)}
</style>
</head>
<body>
<main class="canvas">
  <svg class="rings" width="1200" height="909" viewBox="0 0 1200 909" aria-hidden="true">
    <circle cx="484" cy="446" r="600" fill="var(--ring)"/>
    <circle cx="484" cy="446" r="540" fill="#f4f6fb" stroke="var(--ring-edge)"/>
    <circle cx="484" cy="446" r="470" fill="#f8f9fc" stroke="var(--ring-edge)"/>
    <circle cx="484" cy="446" r="400" fill="#fff" stroke="var(--ring-edge)"/>
  </svg>
  <div class="backdrop"></div>

  <section class="screen left">
    <div class="status"><span>8:48</span><span class="icons">
      <svg width="40" height="10" viewBox="0 0 40 10"><rect x="0" y="6" width="2" height="4" fill="#1d1f24"/><rect x="3" y="4" width="2" height="6" fill="#1d1f24"/><rect x="6" y="2" width="2" height="8" fill="#1d1f24"/><path d="M12 4a6 6 0 0 1 8 0M14 6a3 3 0 0 1 4 0" stroke="#1d1f24" stroke-width="1.4" fill="none"/><rect x="23" y="1" width="15" height="8" rx="2" fill="none" stroke="#1d1f24"/><rect x="24.5" y="2.5" width="5" height="5" fill="#1d1f24"/></svg></span></div>
    <header class="header">
      <div class="menu"><i></i><i></i><i></i></div>
      <div class="driver"><div class="name">Liam Kessler</div><div class="licence">License : 1234567890</div></div>
      <div class="sync"><svg width="12" height="12" viewBox="0 0 12 12"><path d="M2 6l3 3 5-6" stroke="var(--green)" stroke-width="2" fill="none"/></svg><span class="sync-btn">Sync Now</span></div>
    </header>
    <div class="body">
      <div class="card">
        <div class="grid">
          <div class="cell"><div class="value">15:30</div><div class="label">Period<br>Remaining</div></div>
          <div class="cell"><div class="value">0 / 1</div><div class="label">7 hr Rests<br>Found/Required</div></div>
        </div>
        <div class="pager"><span class="btn">&lt; Previous</span><span class="mid"><span class="value">1/1</span><br><span class="label">Active Periods</span></span><span class="btn">Next &gt;</span></div>
      </div>
      <div class="card titled">
        <span class="tab">14 day Rule</span><span class="info">i</span>
        <div class="range"><div><div class="value">01:17 14-Aug</div><div class="label">Period Start</div></div><div class="end"><div class="value">01:17 28-Aug</div><div class="label">Period End</div></div></div>
        <div class="bar-title">Work Completed</div>
        <div class="bar"><span style="width:54%"></span></div>
        <div class="bar-labels"><span>0 hr</span><span>144 hr</span></div>
        <div class="grid">
          <div class="cell"><div class="value">78:08</div><div class="label">Work Completed</div></div>
          <div class="cell"><div class="value">43:01</div><div class="label">Maximum Continuous Rest</div></div>
          <div class="cell"><div class="value">65:52</div><div class="label">Work Remaining</div></div>
          <div class="cell"><div class="value">01:17 27-Aug</div><div class="label">Start 24 hr Rest Before</div></div>
          <div class="cell"><div class="value">62:29</div><div class="label">Period<br>Remaining</div></div>
          <div class="cell"><div class="value">1 / 2</div><div class="label">24 hr Rests<br>Found/Required</div></div>
        </div>
        <div class="pager"><span class="btn">&lt; Previous</span><span class="mid"><span class="value">1/4</span><br><span class="label">Active Periods</span></span><span class="btn">Next &gt;</span></div>
      </div>
      <div class="card titled">
        <span class="tab">Total Work Since Last 24 hr Rest</span>
        <div class="bar"><span style="width:40%"></span></div>
        <div class="bar-labels"><span>0 hr</span><span>84 hr</span></div>
        <div class="grid" style="margin-top:6px">
          <div class="cell"><div class="value">02:33 23-Aug</div><div class="label">End of 24 hr Rest</div></div>
          <div class="cell"><div class="value">33:40</div><div class="label">Work Completed</div></div>
        </div>
      </div>
    </div>
    <nav class="tabbar">
      <span class="tabitem"><svg width="14" height="14" viewBox="0 0 14 14"><path d="M4 3.5a5 5 0 1 0 6 0M7 1v6" stroke="#1d1f24" stroke-width="1.6" fill="none"/></svg>Logout</span>
      <span class="tabitem"><svg width="14" height="14" viewBox="0 0 14 14"><rect x="2" y="1.5" width="9" height="11" rx="1" stroke="#1d1f24" fill="none"/><path d="M4 5h5M4 8h3" stroke="#1d1f24"/></svg>Compliance</span>
    </nav>
    <span class="home-bar"></span>
  </section>

  <section class="screen right">
    <div class="status"><span>8:39</span><span class="icons">
      <svg width="40" height="10" viewBox="0 0 40 10"><rect x="0" y="6" width="2" height="4" fill="#1d1f24"/><rect x="3" y="4" width="2" height="6" fill="#1d1f24"/><rect x="6" y="2" width="2" height="8" fill="#1d1f24"/><path d="M12 4a6 6 0 0 1 8 0M14 6a3 3 0 0 1 4 0" stroke="#1d1f24" stroke-width="1.4" fill="none"/><rect x="23" y="1" width="15" height="8" rx="2" fill="none" stroke="#1d1f24"/><rect x="24.5" y="2.5" width="5" height="5" fill="#1d1f24"/></svg></span></div>
    <header class="header">
      <div class="menu"><i></i><i></i><i></i></div>
      <div class="driver"><div class="name">Liam Kessler</div><div class="licence">License : 1234567890</div></div>
      <div class="sync"><svg width="12" height="12" viewBox="0 0 12 12"><path d="M2 6l3 3 5-6" stroke="var(--green)" stroke-width="2" fill="none"/></svg><span class="sync-btn">Sync Now</span></div>
    </header>
    <div class="body">
      <div class="card">
        <div class="cell" style="border-right:0"><div class="value">17:25</div><div class="label">Total Night Long Work</div></div>
        <div class="grid">
          <div class="cell"><div class="value">17:25</div><div class="label">Night Work</div></div>
          <div class="cell"><div class="value">00:00</div><div class="label">Long Work</div></div>
        </div>
        <div class="pager"><span class="btn">&lt; Previous</span><span class="mid"><span class="value">1/4</span><br><span class="label">Active Periods</span></span><span class="btn">Next &gt;</span></div>
      </div>
      <div class="card titled">
        <span class="tab"><svg width="14" height="10" viewBox="0 0 14 10"><path d="M1 1v8M1 6h12v3M3 4h4" stroke="#fff" stroke-width="1.4" fill="none"/></svg>Night Rests</span><span class="info">i</span>
        <div class="range"><div><div class="value">17 Aug</div><div class="label">Period Start</div></div><div class="end"><div class="value">30 Aug</div><div class="label">Period End</div></div></div>
        <div class="grid">
          <div class="cell"><div class="value">01:00 29-Aug</div><div class="label">Start Next<br>Night Rest Before</div></div>
          <div class="cell"><div class="value">1</div><div class="label">Consecutive<br>Night Rests Required</div></div>
        </div>
        <div class="calendar">
          <span class="day">12</span><span class="day">13</span><span class="day miss">14</span><span class="day miss">15</span><span class="day">16</span><span class="day miss">17</span><span class="day">18</span>
          <span class="day miss">19</span><span class="day miss">20</span><span class="day miss">21</span><span class="day">22</span><span class="day miss">23</span><span class="day miss">24</span><span class="day now">25</span>
        </div>
        <div class="pager"><span class="btn">&lt; Previous</span><span class="btn">Next &gt;</span></div>
      </div>
      <div class="card titled">
        <span class="tab"><svg width="12" height="12" viewBox="0 0 12 12"><rect x="1" y="2" width="10" height="9" rx="1" stroke="#fff" fill="none"/><path d="M4 5l4 4M8 5l-4 4" stroke="#fff"/></svg>24 Hour Continuous Rest</span>
        <p class="note">Green ticks on calendar indicate dates on which a 24 hour continuous rest break ended</p>
        <div class="calendar">
          <span class="day ok">12</span><span class="day ok">13</span><span class="day ok">14</span><span class="day miss">15</span><span class="day miss">16</span><span class="day miss">17</span><span class="day miss">18</span>
          <span class="day ok">19</span><span class="day miss">20</span><span class="day miss">21</span><span class="day miss">22</span><span class="day ok">23</span><span class="day miss">24</span><span class="day miss">25</span>
        </div>
        <p class="foot">24 continuous hours stationary rest time taken after no more than 84 hours work time and 24 continuous hours stationary rest.</p>
      </div>
    </div>
    <nav class="tabbar">
      <span class="tabitem"><svg width="14" height="14" viewBox="0 0 14 14"><path d="M4 3.5a5 5 0 1 0 6 0M7 1v6" stroke="#1d1f24" stroke-width="1.6" fill="none"/></svg>Logout</span>
      <span class="tabitem"><svg width="14" height="14" viewBox="0 0 14 14"><rect x="2" y="1.5" width="9" height="11" rx="1" stroke="#1d1f24" fill="none"/><path d="M4 5h5M4 8h3" stroke="#1d1f24"/></svg>Compliance</span>
      <span class="tabitem"><svg width="14" height="14" viewBox="0 0 14 14"><path d="M1 7l12-5-4 11-2-5z" stroke="#1d1f24" fill="none"/></svg>Send</span>
    </nav>
    <span class="home-bar"></span>
  </section>
</main>
</body>
</html>
```